Market Research firm needs updated business cards with new logo

We need the logo to be included somewhere on the card (attached). We would also like the phrases "Independent, Objective, Comprehensive" and "Research You Can Trust" somewhere on the card. Front or back. Our colors are hex codes 6075a7, e48d25 and 5a5b5b. Though you are certainly not limited to those shades, whatever you produce should coordinate with them. I have also attached our favicon. Feel free to use it in your design, but please do not use it to replace the full logo.

Contact Information for Business Card

see project description

Font styles to use
Other font styles liked:
• Open Sans

Requirements
Must have
• the logo
• We use Open Sans font

```html
<!DOCTYPE html>
<html lang="en">
<head>
<meta charset="utf-8">
<title>Northlake Research – Business Card</title>
<link rel="stylesheet" href="https://fonts.googleapis.com/css2?family=Open+Sans:wght@400;600;700&display=swap">
<style>
  :root {
    --stage: #e9e6e1;
    --card-front: #ffffff;
    --card-back: #6e7d8c;
    --slate: #6b7887;
    --orange: #f0821e;
    --divider: #7a8591;
  }
  * { margin: 0; padding: 0; box-sizing: border-box; }
  html, body { width: 900px; height: 1200px; overflow: hidden; }
  body {
    position: relative;
    background: var(--stage);
    font-family: "Open Sans", Arial, sans-serif;
    color: var(--slate);
  }
  .card {
    position: absolute;
    left: 86px;
    width: 736px;
    height: 430px;
    border-radius: 22px;
    overflow: hidden;
  }
  .card--front {
    top: 137px;
    background: var(--card-front);
    border-bottom: 6px solid var(--orange);
  }
  .card--back {
    top: 633px;
    background: var(--card-back);
  }
  .wordmark {
    position: absolute;
    left: 0; right: 0;
    top: 62px;
    text-align: center;
    font-size: 50px;
    font-weight: 600;
    letter-spacing: -0.5px;
    color: var(--orange);
    line-height: 1;
  }
  .values {
    position: absolute;
    left: 0; right: 0;
    top: 129px;
    text-align: center;
    font-size: 18px;
    letter-spacing: 1px;
    color: var(--slate);
  }
  .person {
    position: absolute;
    right: 381px;
    top: 246px;
    text-align: right;
  }
  .person__name {
    font-size: 28px;
    font-weight: 700;
    line-height: 36px;
    color: var(--slate);
  }
  .person__role {
    font-size: 17px;
    line-height: 22px;
    color: var(--orange);
  }
  .divider {
    position: absolute;
    left: 374px;
    top: 244px;
    width: 2px;
    height: 66px;
    background: var(--divider);
  }
  .contacts {
    position: absolute;
    left: 396px;
    top: 238px;
    list-style: none;
  }
  .contacts li {
    display: flex;
    align-items: center;
    height: 25.5px;
    font-size: 17px;
    color: var(--slate);
  }
  .contacts svg { width: 14px; height: 14px; margin-right: 14px; flex: none; }
  .contacts .accent { color: var(--orange); }
  .slogan {
    position: absolute;
    left: 0; right: 0;
    top: 368px;
    text-align: center;
    font-size: 18px;
    letter-spacing: 1px;
    color: var(--slate);
  }
  .back-mark {
    position: absolute;
    left: 0; right: 0;
    top: 198px;
    text-align: center;
    font-size: 28px;
    font-weight: 600;
    color: var(--orange);
  }
</style>
</head>
<body>
  <section class="card card--front">
    <div class="wordmark">Northlake Research</div>
    <div class="values">Independent &nbsp;|&nbsp; Objective &nbsp;|&nbsp; Comprehensive</div>

    <div class="person">
      <div class="person__name">Daniel Marsh</div>
      <div class="person__role">CEO</div>
    </div>
    <div class="divider"></div>
    <ul class="contacts">
      <li>
        <svg viewBox="0 0 14 14" aria-hidden="true"><rect x="3.5" y="1" width="7" height="12" rx="1.5" fill="none" stroke="#f0821e" stroke-width="1.6"/><line x1="6" y1="10.8" x2="8" y2="10.8" stroke="#f0821e" stroke-width="1.4"/></svg>
        000 000 0000
      </li>
      <li>
        <svg viewBox="0 0 14 14" aria-hidden="true"><rect x="1" y="3" width="12" height="8.5" fill="none" stroke="#f0821e" stroke-width="1.6"/><polyline points="1.5,3.5 7,8 12.5,3.5" fill="none" stroke="#f0821e" stroke-width="1.4"/></svg>
        <span>dmarsh@<span class="accent">northlakeresearch</span>.com</span>
      </li>
      <li>
        <svg viewBox="0 0 14 14" aria-hidden="true"><circle cx="8" cy="6" r="4.2" fill="none" stroke="#f0821e" stroke-width="1.6"/><line x1="5" y1="9" x2="1.5" y2="12.5" stroke="#f0821e" stroke-width="1.8"/></svg>
        <span>www.<span class="accent">northlakeresearch</span>.com</span>
      </li>
    </ul>
    <div class="slogan">Research You Can Trust</div>
  </section>

  <section class="card card--back">
    <div class="back-mark">Northlake Research</div>
  </section>
</body>
</html>
```